Calvanto Group Real Estate Company business cards

New business card design, we are generally happy with the basic layout of the existing front of business card, (feel free to change) but require a head shot photo on the back side.

http://www.calvanto.com.au/

Attached logos, and existing business card

------------------------------

Target Market(s)

Real estate

Industry/Entity Type

Real Estate

Contact Information for Business Card

Standard size double sided

Font styles to use
Other font styles liked:
• Futura

Requirements
Must have
• Photo head shot on the back side
Nice to have
• yes
Should not have
• No

```html
<!DOCTYPE html>
<html lang="en">
<head>
<meta charset="utf-8">
<title>Calvanto Group business cards</title>
<link rel="stylesheet" href="https://fonts.googleapis.com/css2?family=Jost:wght@400;500;700&display=swap">
<style>
  :root{
    --bg:#e4e4e4;
    --card:#f7f7f8;
    --purple:#3c1d5e;
    --purple-deep:#2a1145;
    --orange:#f0901e;
    --ink:#2b2440;
    --muted:#9a98a2;
    --photo-a:#cfd3da;
    --photo-b:#2b3550;
  }
  *{box-sizing:border-box;margin:0;padding:0}
  html,body{width:1200px;height:1200px;overflow:hidden}
  body{background:var(--bg);font-family:"Jost",sans-serif;color:var(--ink);position:relative}
  .card{position:absolute;left:250px;width:700px;height:400px;background:var(--card);border-radius:26px;overflow:hidden;box-shadow:0 6px 18px rgba(0,0,0,.18)}
  .card--front{top:150px}
  .card--back{top:640px}
  .card svg.shapes{position:absolute;inset:0}
  /* front */
  .headshot{position:absolute;left:0;bottom:0;width:330px;height:290px;background:linear-gradient(180deg,var(--photo-a) 0%,#b9aaa0 45%,var(--photo-b) 75%)}
  .tagline{position:absolute;right:70px;top:48px;text-align:left;font-size:30px;line-height:1.05;letter-spacing:.5px;color:var(--ink)}
  .tagline span{display:block;color:var(--orange)}
  .brand{position:absolute;font-weight:500;color:var(--purple-deep);letter-spacing:1px;line-height:1}
  .card--front .brand{left:360px;top:165px;font-size:64px}
  .brand-sub{display:block;text-align:right;font-size:.18em;letter-spacing:.6em;color:var(--muted);margin-top:4px}
  /* back */
  .person{position:absolute;right:60px;top:30px;text-align:right;color:#fff}
  .person-name{font-weight:700;font-size:26px}
  .person-role{font-size:16px}
  .contacts{position:absolute;left:60px;top:180px;list-style:none;font-size:19px;color:var(--ink)}
  .contacts li{display:flex;align-items:center;gap:14px;height:30px}
  .contacts svg{width:18px;height:18px;flex:none}
  .card--back .brand{left:60px;top:285px;font-size:72px}
  .find{position:absolute;right:50px;top:200px;font-size:18px;text-align:right;line-height:1.5}
  .social{display:inline-flex;gap:5px;vertical-align:middle;margin-left:6px}
  .social i{width:20px;height:20px;border-radius:5px;background:var(--orange);display:block}
</style>
</head>
<body>

<section class="card card--front">
  <svg class="shapes" width="700" height="400" viewBox="0 0 700 400">
    <rect x="300" y="368" width="400" height="32" fill="var(--purple-deep)"/>
  </svg>
  <div class="headshot" role="img" aria-label="Head shot of the director in a dark suit and blue tie on a white background"></div>
  <p class="tagline">Let us show you<span>property</span></p>
  <div class="brand">calvanto<span class="brand-sub">GROUP</span></div>
</section>

<section class="card card--back">
  <svg class="shapes" width="700" height="400" viewBox="0 0 700 400">
    <path d="M0 0 H700 V95 C560 110 440 130 330 150 C200 172 80 150 0 120 Z" fill="var(--purple)"/>
    <path d="M0 150 C90 120 180 95 300 115 C430 135 560 100 700 90 L700 100 C560 115 430 150 300 130 C190 112 100 130 0 165 Z" fill="var(--orange)"/>
    <path d="M0 120 C80 150 200 172 330 150 C200 150 90 140 0 140 Z" fill="var(--orange)"/>
  </svg>
  <div class="person">
    <div class="person-name">Daniel Tran</div>
    <div class="person-role">Director</div>
  </div>
  <ul class="contacts">
    <li><svg viewBox="0 0 18 18"><rect x="4" y="1" width="10" height="16" rx="2" fill="var(--orange)"/><rect x="6" y="3" width="6" height="10" fill="#fff"/></svg>0412 555 031</li>
    <li><svg viewBox="0 0 18 18"><circle cx="9" cy="9" r="8" fill="var(--orange)"/><path d="M1 9H17M9 1C5 5 5 13 9 17M9 1C13 5 13 13 9 17" stroke="#fff" stroke-width="1.2" fill="none"/></svg>www.calvanto.com.au</li>
    <li><svg viewBox="0 0 18 18"><rect x="1" y="4" width="16" height="11" rx="1" fill="var(--orange)"/><path d="M1 4L9 10L17 4" stroke="#fff" stroke-width="1.4" fill="none"/></svg>daniel.tran@calvanto.com.au</li>
  </ul>
  <div class="brand">calvanto<span class="brand-sub">GROUP</span></div>
  <div class="find">
    <div>Find us:<span class="social"><i></i><i></i><i></i></span></div>
    <div>ABN: 41 208 653 907</div>
  </div>
</section>

</body>
</html>
```